Professional and creative business card design for recruiting service providers

Our company supports German medium-sized companies in filling vacancies promptly. For this we use social media marketing and bring our customers into the visibility.

We want a professional but also creative design for our business cards.

Please look at lindqvar-staff.de to get an impression of our CI.

Target Market(s)

Small and medium-sized companies in Germany from the industry

Industry/Entity Type

Industrie, Handwerk

Contact Information for Business Card

Name, Position, Telefonnummer, Email, Website

Colors
EE7325
F08F49
F5BC92
FAE3D3
FDF4ED

Requirements
Must have
• A picture of the employee and in the style of www.lindqvar-staff.de

```html
<!DOCTYPE html>
<html lang="de">
<head>
<meta charset="utf-8">
<title>Lindqvar &amp; Staff – Visitenkarte</title>
<link rel="stylesheet" href="https://fonts.googleapis.com/css2?family=Montserrat:wght@700;800&family=Arimo:wght@400&display=swap">
<style>
  :root {
    --brand-orange: #EE5F2C;
    --brand-orange-deep: #E35222;
    --ink: #111111;
    --paper: #FFFFFF;
    --photo-bg: #E2E0E2;
    --photo-suit: #2A2C35;
    --stage: #3A3A3C;
  }
  * { box-sizing: border-box; margin: 0; padding: 0; }
  html, body { width: 1200px; height: 1015px; overflow: hidden; }
  body {
    background: var(--stage);
    font-family: "Arimo", Arial, sans-serif;
    position: relative;
  }
  .card {
    position: absolute;
    left: 290px;
    width: 620px;
    height: 354px;
    overflow: hidden;
    box-shadow: 0 14px 30px rgba(0,0,0,.45);
  }
  /* front */
  .card--front { top: 100px; background: var(--brand-orange); }
  .front__name {
    position: absolute;
    right: 52px;
    bottom: 78px;
    color: var(--paper);
    font-family: "Montserrat", Arial, sans-serif;
    font-weight: 800;
    font-size: 40px;
    line-height: 1.05;
    letter-spacing: 3px;
    text-align: left;
  }
  /* back */
  .card--back { top: 520px; background: var(--paper); }
  .back__band {
    position: absolute; left: 0; right: 0; bottom: 0;
    height: 14px; background: var(--brand-orange);
  }
  .back__brand {
    position: absolute; left: 44px; top: 88px;
    display: flex; align-items: center; gap: 16px;
  }
  .back__brand-mark {
    width: 44px; height: 44px; background: var(--brand-orange);
  }
  .back__brand-name {
    font-family: "Montserrat", Arial, sans-serif;
    font-weight: 800; font-size: 27px; line-height: 1.05;
    letter-spacing: 2px; color: var(--ink);
  }
  .contact {
    position: absolute; left: 44px; top: 222px;
    list-style: none; font-size: 17px; color: var(--ink);
  }
  .contact li { display: flex; align-items: center; gap: 10px; margin-bottom: 7px; }
  .contact svg { width: 18px; height: 18px; flex: none; }
  .portrait {
    position: absolute; right: 40px; top: 36px;
    width: 236px; height: 208px;
    border: 3px solid var(--brand-orange);
    background: linear-gradient(180deg, var(--photo-bg) 0%, var(--photo-bg) 55%, var(--photo-suit) 100%);
  }
  .person {
    position: absolute; right: 40px; top: 258px; width: 236px;
    text-align: center;
  }
  .person__name {
    font-family: "Montserrat", Arial, sans-serif;
    font-weight: 800; font-size: 21px; letter-spacing: 1px; color: var(--ink);
  }
  .person__role { font-size: 14px; letter-spacing: 1px; color: var(--ink); margin-top: 3px; }
</style>
</head>
<body>
  <section class="card card--front">
    <div class="front__name">LINDQVAR<br>&amp; STAFF</div>
  </section>

  <section class="card card--back">
    <div class="back__brand">
      <span class="back__brand-mark"></span>
      <div class="back__brand-name">LINDQVAR<br>&amp; STAFF</div>
    </div>

    <ul class="contact">
      <li>
        <svg viewBox="0 0 24 24"><path fill="#EE5F2C" d="M6.6 10.8a15.1 15.1 0 0 0 6.6 6.6l2.2-2.2c.3-.3.7-.4 1-.2 1.1.4 2.3.6 3.6.6.6 0 1 .4 1 1V20c0 .6-.4 1-1 1A17 17 0 0 1 3 4c0-.6.4-1 1-1h3.5c.6 0 1 .4 1 1 0 1.3.2 2.5.6 3.6.1.3 0 .7-.2 1z"/></svg>
        030-555 018 274
      </li>
      <li>
        <svg viewBox="0 0 24 24"><path fill="#EE5F2C" d="M2 5h20v14H2z"/><path d="M2 5l10 8 10-8" fill="none" stroke="#fff" stroke-width="1.6"/></svg>
        info@lindqvar-staff.de
      </li>
      <li>
        <svg viewBox="0 0 24 24"><g fill="none" stroke="#EE5F2C" stroke-width="2"><circle cx="12" cy="12" r="9"/><path d="M3 12h18M12 3c3 3 3 15 0 18M12 3c-3 3-3 15 0 18"/></g></svg>
        www.lindqvar-staff.de
      </li>
    </ul>

    <div class="portrait" role="img" aria-label="Porträtfoto des Geschäftsführers vor hellgrauem Hintergrund"></div>
    <div class="person">
      <div class="person__name">MALTE BRANDES</div>
      <div class="person__role">MANAGING DIRECTOR</div>
    </div>

    <div class="back__band"></div>
  </section>
</body>
</html>
```